Nora Flintwick Music EP Design Artwork

EP musical recording cover art work. Nora Flintwick is a new artist in the Pop, Country Pop, Pop Rock, Americana and Singer-songwriter genres. The name of the EP is "Paper Kites at Noon", and her first single is being released on all streaming platforms globally June 1st. We are looking for a graphic design that has that Pop/rock female artist appeal. norafintwick.net and all social media outlets are noraflintwicksongs (reference). Your art work will be seen globally and we will give a personal shout out on all her socials to the design we select as a single post. Her signature logo is attached for a color and style example. Please try to use the signature within the EP cover design, but feel free to change the purple backing accordingly if another color is needed to fit better with the color scheme of your design.

Requirements
Must have
• Nora Flintwick signature logo and EP name

Some of you asked for hi res pics, use this link:

https://files.vantrelbox.net/share/u/0/folders/8KqTz3LmW0pRx7YvN2cJhD5sAa9EgUoiB
Should not have
• June 1 on the EP art work. June 1 is the release of the first single on the EP. This is an album cover, we want it to look like a really cool pop female artist album cover, thanks.

```html
<!DOCTYPE html>
<html lang="en">
<head>
<meta charset="utf-8">
<title>Paper Kites at Noon – Nora Flintwick</title>
<link rel="stylesheet" href="https://fonts.googleapis.com/css2?family=Anton&display=swap">
<style>
  :root {
    --stage: #b4b4b4;
    --navy: #0c3a4f;
    --navy-deep: #06121f;
    --butter: #f5eca3;
    --butter-pale: #fbf5c9;
    --cream: #f8efc2;
    --white: #ffffff;
  }
  * { margin: 0; padding: 0; box-sizing: border-box; }
  html, body {
    width: 1200px;
    height: 900px;
    overflow: hidden;
    background: var(--stage);
  }
  .stage {
    width: 1200px;
    height: 900px;
    display: flex;
    align-items: center;
    justify-content: center;
  }
  .ep-cover {
    width: 860px;
    height: 860px;
    display: block;
  }
  .title-line {
    font-family: "Anton", "Oswald", sans-serif;
    font-size: 240px;
    filter: url(#title-shadow);
  }
  .title-line--first { fill: var(--cream); }
  .title-line--second { fill: var(--white); }
  .artist-name {
    font-family: "Anton", "Oswald", sans-serif;
    font-size: 50px;
    fill: var(--cream);
  }
</style>
</head>
<body>
<main class="stage">
  <svg class="ep-cover" viewBox="0 0 1000 1000" xmlns="http://www.w3.org/2000/svg" aria-labelledby="cover-title">
    <title id="cover-title">Paper Kites at Noon – Nora Flintwick EP cover</title>
    <defs>
      <filter id="title-shadow" x="-10%" y="-10%" width="130%" height="130%">
        <feDropShadow dx="6" dy="5" stdDeviation="0" flood-color="#06121f" flood-opacity="1"/>
      </filter>
      <linearGradient id="photo-tones" x1="0" y1="0" x2="0" y2="1">
        <stop offset="0" stop-color="#c9a35e"/>
        <stop offset="0.3" stop-color="#3a342c"/>
        <stop offset="0.6" stop-color="#d6c38e"/>
        <stop offset="1" stop-color="#3a3330"/>
      </linearGradient>
      <clipPath id="cover-clip"><rect width="1000" height="1000"/></clipPath>
    </defs>

    <g clip-path="url(#cover-clip)">
      <rect class="cover-ground" width="1000" height="1000" fill="var(--navy)"/>
      <polygon class="cover-sun-panel" points="0,0 108,0 490,1000 0,1000" fill="var(--butter)"/>
      <circle class="cover-glow" cx="20" cy="110" r="115" fill="var(--butter-pale)"/>
      <circle class="cover-glow" cx="20" cy="860" r="125" fill="var(--butter-pale)"/>

      <rect class="artist-photo" x="55" y="70" width="455" height="910" rx="40"
            fill="url(#photo-tones)"
            role="img" aria-label="Photo of the artist smiling, crouching in a black jacket, beige trousers and black heeled boots"/>

      <text class="title-line title-line--first" transform="translate(732,795) rotate(-90)"
            textLength="740" lengthAdjust="spacingAndGlyphs">PAPER KITES</text>
      <text class="title-line title-line--second" transform="translate(968,795) rotate(-90)"
            textLength="740" lengthAdjust="spacingAndGlyphs">AT NOON</text>

      <text class="artist-name" x="615" y="930"
            textLength="330" lengthAdjust="spacingAndGlyphs">NORA FLINTWICK</text>
    </g>
  </svg>
</main>
</body>
</html>
```